New business card for a regional office of a US M&A company

We need business card for a finance company, office based in Hong Kong , our Head office is in US, our business is to Merge and acquires companies , the new office will be a regional office for the Asia Pacific region. We want to use the head office logo as attached ( but don't have to be exactly the same, can be a variation to it) as a base and then add Asia Pacific alongside the logo.
We would prefer to have be bilingual Eng + Chinese, although we don't really have Chinese company name .

Industry/Entity Type

Business

Contact Information for Business Card

Clara Jo Tsang
 

VP,
APAC M&A Operations
Orin Vantage Asia Pacific Limited
 
Unit 1407, K18
18 Tai Lok Shan Road, 
Hong Kong 
 
M: +852 6038 1742
T : +852 2836 4100
F : +852 2836 4177
VOIP: 4158
 
cjtsang@orinvantage.com

Font styles to use
Serif
Sans Serif

Colors

Designer to choose colors to be used in the design.

Requirements
Must have
• APAC Office

```html
<!DOCTYPE html>
<html lang="en">
<head>
<meta charset="utf-8">
<title>Orin Vantage – Business Card</title>
<link href="https://fonts.googleapis.com/css2?family=Open+Sans:wght@400;600;700;800&display=swap" rel="stylesheet">
<style>
  :root {
    --teal: #1fb0cb;
    --navy: #14304f;
    --ink: #5a5f66;
    --paper: #ffffff;
    --backdrop: #e9ebee;
  }
  * { box-sizing: border-box; margin: 0; padding: 0; }
  html, body { width: 1200px; height: 810px; overflow: hidden; }
  body {
    background: var(--backdrop);
    font-family: "Open Sans", Arial, sans-serif;
    position: relative;
  }
  .card {
    position: absolute;
    width: 640px;
    height: 372px;
    overflow: hidden;
    box-shadow: 0 10px 28px rgba(0,0,0,.22);
  }

  /* Shared brand lockup */
  .brand { text-align: center; }
  .brand-name {
    display: block;
    font-weight: 800;
    letter-spacing: 1px;
    line-height: 1.1;
  }
  .brand-region {
    display: block;
    font-weight: 600;
    letter-spacing: 4px;
    margin-top: 6px;
  }

  /* Front */
  .card-front { left: 90px; top: 50px; background: var(--teal); }
  .card-front .brand {
    position: absolute;
    left: 0; right: 0; top: 140px;
  }
  .card-front .brand-name { font-size: 46px; color: var(--navy); }
  .card-front .brand-region { font-size: 15px; color: var(--navy); }

  /* Back */
  .card-back { left: 480px; top: 400px; background: var(--paper); }
  .card-back .brand {
    position: absolute;
    left: 14px; top: 120px;
    width: 330px;
  }
  .card-back .brand-name { font-size: 36px; color: var(--teal); }
  .card-back .brand-region { font-size: 13px; color: var(--navy); }
  .divider {
    position: absolute;
    left: 352px; top: 56px;
    width: 1.5px; height: 180px;
    background: var(--teal);
  }
  .contact {
    position: absolute;
    left: 372px; top: 50px;
    width: 260px;
    color: var(--ink);
  }
  .contact-name { color: var(--teal); font-size: 22px; font-weight: 600; line-height: 1.1; }
  .contact-title { color: var(--navy); font-size: 12px; font-weight: 700; margin-bottom: 10px; }
  .contact-list { list-style: none; font-size: 13.5px; line-height: 1.45; }
  .contact-list li { display: flex; align-items: center; gap: 9px; }
  .contact-list svg { width: 11px; height: 11px; fill: var(--teal); flex: none; }
  .contact-address { font-size: 14.5px; line-height: 1.35; margin-top: 12px; }
  .back-wave { position: absolute; left: 0; bottom: 0; width: 640px; height: 140px; }
  .voip {
    position: absolute;
    left: 96px; bottom: 16px;
    color: var(--paper);
    font-size: 15px;
    letter-spacing: .5px;
  }
</style>
</head>
<body>

<section class="card card-front" aria-label="Card front">
  <div class="brand">
    <span class="brand-name">ORIN VANTAGE</span>
    <span class="brand-region">ASIA PACIFIC</span>
  </div>
</section>

<section class="card card-back" aria-label="Card back">
  <div class="brand">
    <span class="brand-name">ORIN VANTAGE</span>
    <span class="brand-region">ASIA PACIFIC</span>
  </div>

  <div class="divider"></div>

  <div class="contact">
    <p class="contact-name">Clara Jo Tsang</p>
    <p class="contact-title">VP, APAC M&amp;A Operations</p>
    <ul class="contact-list">
      <li><svg viewBox="0 0 12 12"><rect x="3" y="0" width="6" height="12" rx="1"/><rect x="4" y="1.5" width="4" height="7" fill="#fff"/></svg>+852 6038 1742</li>
      <li><svg viewBox="0 0 12 12"><path d="M2.5 0.5l2 2.5-1.2 1.3c.8 1.7 2.1 3 3.7 3.8L8.3 6.8l2.7 2-1 2.4C5 11 1 7 .8 2z"/></svg>+852 2836 4100</li>
      <li><svg viewBox="0 0 12 12"><rect x="3" y="0" width="6" height="4"/><rect x="0" y="4" width="12" height="6" rx="1"/><rect x="3" y="8" width="6" height="4" fill="#fff"/></svg>+852 2836 4177</li>
      <li><svg viewBox="0 0 12 12"><rect x="0" y="2" width="12" height="8"/><path d="M0 2l6 4.5L12 2" fill="none" stroke="#fff" stroke-width="1.2"/></svg>cjtsang@orinvantage.com</li>
    </ul>
    <p class="contact-address">Unit 1407, K18 18 Tai Lok<br>Shan Road, Hong Kong</p>
  </div>

  <svg class="back-wave" viewBox="0 0 640 140" preserveAspectRatio="none" aria-hidden="true">
    <path d="M0 140 L0 100 C120 20 240 80 360 70 C470 62 570 20 640 0 L640 140 Z" fill="var(--teal)"/>
    <path d="M0 96 C120 12 240 72 360 62 C470 54 570 12 640 -6" fill="none" stroke="var(--navy)" stroke-width="5"/>
  </svg>
  <p class="voip">VOIP: 4158</p>
</section>

</body>
</html>
```